New Website for Manufacturing Company - PSD only, no coding - CLOSED TO NEW DESIGNERS

IF YOU HAVE NOT ALREADY SUBMITTED A DESIGN PLEASE DO NOT SUBMIT ONE.
This is a re-work of an existing website. We can keep the themes and color schemes the same but we will be changing the layout and page content.
The scope includes the creation of some icons/sketches that will form some of the page content.
The scope is design only, no coding.
There are four files that have been uploaded that give a more detailed project brief, please read them.
Target Market(s)
Manufacturing
Industry/Entity Type
It Company
Number of Pages Required
1 page

```html
<!DOCTYPE html>
<html lang="en">
<head>
<meta charset="utf-8">
<title>K.L Marquez — Modular Buildings</title>
<link href="https://fonts.googleapis.com/css2?family=Open+Sans:wght@400;600;700&family=Roboto:wght@300;400;500;700&display=swap" rel="stylesheet">
<style>
:root{
  --orange:#f28a2e;
  --orange-dark:#d9741c;
  --ink:#2b2b2b;
  --muted:#777;
  --dark:#262626;
  --darker:#1d1d1d;
  --footer:#222;
  --white:#fff;
}
*{box-sizing:border-box;margin:0;padding:0}
html,body{width:1200px;height:3172px;overflow:hidden}
body{font-family:"Open Sans",Arial,sans-serif;color:var(--ink);background:var(--white);position:relative}
.site-header{height:136px;display:flex;align-items:center;padding:0 28px;background:var(--white);position:relative}
.brand{display:flex;align-items:center;gap:18px}
.brand-mark{width:76px;height:76px;border-radius:50%;background:var(--ink)}
.brand-name{font-family:"Roboto",sans-serif;font-weight:700;font-size:36px;color:var(--ink);letter-spacing:.5px}
.call{margin-left:auto;margin-right:250px;display:flex;align-items:center;gap:14px}
.call-icon{width:44px;height:44px;border-radius:50%;background:var(--ink);display:flex;align-items:center;justify-content:center}
.call-label{font-size:11px;color:var(--muted);text-transform:uppercase;letter-spacing:.5px}
.call-number{font-family:"Roboto",sans-serif;font-size:30px;font-weight:700;color:var(--orange);line-height:1}
.social-top{position:absolute;right:30px;top:48px;display:flex;gap:8px}
.social-top span{width:24px;height:24px;background:var(--orange);display:block}
.main-nav{height:40px;background:var(--orange);display:flex;align-items:stretch;padding:0 40px}
.main-nav a{color:var(--white);text-decoration:none;font-size:14px;font-weight:600;display:flex;align-items:center;padding:0 26px}
.main-nav a.active{background:var(--orange-dark)}
.nav-tools{margin-left:auto;display:flex;gap:26px;align-items:center;color:var(--white);font-size:13px}
.nav-tools span{display:flex;align-items:center;gap:8px}
.hero{position:relative;height:580px;background:linear-gradient(160deg,#9fb2c4 0%,#7e8a92 35%,#5b4b3e 60%,#3b3029 100%)}
.hero-arrow{position:absolute;top:240px;width:44px;height:44px;border-radius:50%;background:rgba(0,0,0,.55);display:flex;align-items:center;justify-content:center}
.hero-arrow.prev{left:70px}.hero-arrow.next{right:70px}
.search-bar{position:absolute;left:0;right:0;bottom:40px;height:64px;background:rgba(30,30,30,.82);display:flex;align-items:center;justify-content:center;gap:14px}
.search-bar .field{width:170px;height:34px;background:var(--white);font-size:11px;color:#999;display:flex;align-items:center;padding:0 12px}
.search-bar .btn{width:140px;height:36px;background:var(--orange);color:var(--white);font-weight:700;font-size:14px;display:flex;align-items:center;justify-content:center}
.welcome{text-align:center;padding:60px 0 0}
.section-title{font-family:"Roboto",sans-serif;font-weight:400;font-size:34px;line-height:1.3;color:var(--ink)}
.rule{width:70px;height:3px;background:var(--orange);margin:18px auto}
.welcome p{width:960px;margin:0 auto;font-size:13px;line-height:1.75;color:var(--muted)}
.offer{text-align:center;padding-top:70px}
.offer .section-title{font-size:38px;font-weight:500}
.cards{display:flex;gap:36px;justify-content:center;margin-top:60px}
.card{width:320px;text-align:left}
.card-photo{height:196px}
.card h3{font-size:12px;font-weight:700;margin:20px 0 8px}
.card p{font-size:12px;color:var(--muted);line-height:1.6;height:40px}
.card-foot{display:flex;justify-content:space-between;align-items:center;margin-top:26px}
.card-foot .more{font-size:14px;font-weight:700}
.price{background:var(--orange);color:var(--white);font-size:12px;font-weight:700;padding:8px 14px}
.view-more{width:248px;height:64px;margin:74px auto 0;background:var(--orange);color:var(--white);font-size:20px;font-weight:600;display:flex;align-items:center;justify-content:center}
.projects{position:absolute;top:1792px;left:0;width:1200px;height:1036px;background:var(--dark);color:var(--white)}
.projects .section-title{color:var(--white);text-align:center;margin-top:62px;font-size:40px}
.tabs{display:flex;align-items:center;margin:48px 76px 0;gap:44px;font-size:14px;font-weight:600}
.tabs .active{border-bottom:2px solid var(--orange);padding-bottom:6px}
.tabs .arrows{margin-left:auto;display:flex;gap:18px}
.tabs-line{height:1px;background:#444;margin:6px 76px 0}
.grid{display:grid;grid-template-columns:repeat(3,320px);column-gap:36px;row-gap:48px;justify-content:center;margin-top:34px}
.project-photo{height:214px}
.project h4{font-family:"Roboto",sans-serif;font-size:20px;font-weight:500;margin:16px 0 6px}
.project p{font-size:12px;color:#aaa;line-height:1.55}
.footer{position:absolute;top:2828px;left:0;width:1200px;height:292px;background:var(--footer);color:#bbb;display:flex;padding:60px 76px 0}
.footer h5{color:var(--white);font-size:13px;font-weight:700;margin-bottom:22px;text-transform:uppercase}
.f-col{width:420px}
.f-col.social{width:200px}
.f-line{display:flex;gap:10px;align-items:center;font-size:12px;margin-bottom:10px}
.f-line i{width:10px;height:10px;background:var(--orange);border-radius:50%;display:block}
.sold-item{display:flex;gap:14px;margin-bottom:16px}
.sold-thumb{width:80px;height:54px;background:linear-gradient(135deg,#8796a4,#4d545a)}
.sold-item p{font-size:12px;line-height:1.5}
.sold-item b{color:var(--orange);font-size:12px}
.social-row{display:flex;gap:10px}
.social-row span{width:36px;height:36px;background:#3a3a3a;display:block}
.bottom-bar{position:absolute;top:3120px;left:0;width:1200px;height:52px;background:var(--darker);color:#888;font-size:12px;display:flex;align-items:center;justify-content:space-between;padding:0 76px}
</style>
</head>
<body>
<header class="site-header">
  <div class="brand"><div class="brand-mark"></div><span class="brand-name">K.L MARQUEZ</span></div>
  <div class="call">
    <div class="call-icon"><svg width="20" height="20" viewBox="0 0 24 24"><path fill="#fff" d="M6.6 10.8a15 15 0 0 0 6.6 6.6l2.2-2.2c.3-.3.7-.4 1-.2 1.1.4 2.3.6 3.6.6.6 0 1 .4 1 1V20c0 .6-.4 1-1 1A17 17 0 0 1 3 4c0-.6.4-1 1-1h3.5c.6 0 1 .4 1 1 0 1.3.2 2.5.6 3.6.1.3 0 .7-.2 1z"/></svg></div>
    <div><div class="call-label">Call us now without hesitation</div><div class="call-number">888-555-0147</div></div>
  </div>
  <div class="social-top"><span></span><span></span><span></span><span></span></div>
</header>
<nav class="main-nav">
  <a class="active">Home</a><a>Gallery</a><a>Blog</a><a>Appointment</a><a>Contact</a>
  <div class="nav-tools"><span>♥ Wishlist</span><span>● My Account</span></div>
</nav>
<section class="hero" role="img" aria-label="Photo of a modular office building with wooden ramp and railings">
  <div class="hero-arrow prev"><svg width="14" height="14" viewBox="0 0 10 10"><path d="M7 1L3 5l4 4" stroke="#fff" stroke-width="1.6" fill="none"/></svg></div>
  <div class="hero-arrow next"><svg width="14" height="14" viewBox="0 0 10 10"><path d="M3 1l4 4-4 4" stroke="#fff" stroke-width="1.6" fill="none"/></svg></div>
  <div class="search-bar"><div class="field">Location</div><div class="field">Building type</div><div class="field">Min size</div><div class="field">Max price</div><div class="field">Sale or lease</div><div class="btn">SEARCH</div></div>
</section>
<section class="welcome">
  <h1 class="section-title">Welcome to K.L<br>MARQUEZ</h1>
  <div class="rule"></div>
  <p>K.L Marquez Modular specializes in the sales and leasing of new and used modular buildings in order to meet clients' specific construction needs at cost effective value. We have over 25 years of experience in the modular building industry, and specialize in permanent and temporary modular construction projects. We cater to a variety of industries including education, healthcare, commercial, retail, childcare, religion, and government sectors. Through our affiliate general engineering and contracting company, K.L Marquez, we provide clients with turnkey projects from conception to resource, including design, site preparation, installation, site improvements, and renovation/relocation of modular buildings.</p>
</section>
<section class="offer">
  <h2 class="section-title">We do sales, leasing, and design-build of new and<br>used commercial modular buildings</h2>
  <div class="rule"></div>
  <div class="cards">
    <article class="card"><div class="card-photo" role="img" aria-label="Photo of modern glass office towers" style="background:linear-gradient(160deg,#a9c6e2,#5f7f9c)"></div><h3>1563 Harlow Bend , Connecticut</h3><p>Nam at amet tempor lorem. Nam porta dui sed.</p><div class="card-foot"><span class="more">Know More</span><span class="price">$250 / Month</span></div></article>
    <article class="card"><div class="card-photo" role="img" aria-label="Photo of an office worker at a desk" style="background:linear-gradient(160deg,#d7d2cf,#8a7c78)"></div><h3>1563 Harlow Bend , Connecticut</h3><p>Nam at amet tempor lorem. Nam porta dui sed.</p><div class="card-foot"><span class="more">Know More</span><span class="price">$250 / Month</span></div></article>
    <article class="card"><div class="card-photo" role="img" aria-label="Photo of a shopping mall interior" style="background:linear-gradient(160deg,#e9dcc4,#9c8566)"></div><h3>1563 Harlow Bend , Connecticut</h3><p>Nam at amet tempor lorem. Nam porta dui sed.</p><div class="card-foot"><span class="more">Know More</span><span class="price">$275 / Month</span></div></article>
  </div>
  <div class="view-more">View More</div>
</section>
<section class="projects">
  <h2 class="section-title">Our Latest Projects</h2>
  <div class="rule"></div>
  <div class="tabs"><span>Commercial Apartment</span><span>Shopping Center</span><span class="active">Office</span>
    <span class="arrows"><svg width="10" height="14" viewBox="0 0 10 14"><path d="M8 1L2 7l6 6" stroke="#fff" stroke-width="2" fill="none"/></svg><svg width="10" height="14" viewBox="0 0 10 14"><path d="M2 1l6 6-6 6" stroke="#fff" stroke-width="2" fill="none"/></svg></span></div>
  <div class="tabs-line"></div>
  <div class="grid">
    <div class="project"><div class="project-photo" role="img" aria-label="Photo of a modular building with a sign" style="background:linear-gradient(160deg,#b7c6d3,#6d6f6c)"></div><h4>Sed faucibus est</h4><p>In rhoncus urna quam, a maximus tortor dapibus eget. Nullam iaculis, ex id.</p></div>
    <div class="project"><div class="project-photo" role="img" aria-label="Photo of a modular unit on a site" style="background:linear-gradient(160deg,#a6c3e0,#7b7a74)"></div><h4>In rhoncus urna quam</h4><p>Praesent consectetur arcu ligula, in ullamcorper nisi vestibulum sollicitudin.</p></div>
    <div class="project"><div class="project-photo" role="img" aria-label="Photo of a crane lifting a modular section" style="background:linear-gradient(160deg,#c7d8ea,#8d8f8a)"></div><h4>Fusce mattis volutpat</h4><p>Sed faucibus est maximus urna congue ullamcorper. Mauris sagittis in erat ut finibus.</p></div>
    <div class="project"><div class="project-photo" role="img" aria-label="Photo of a white modular building" style="background:linear-gradient(160deg,#c9d4dc,#6f6a60)"></div><h4>Duis vulputate felis</h4><p>Sed faucibus est maximus urna congue ullamcorper. Mauris sagittis in erat ut finibus.</p></div>
    <div class="project"><div class="project-photo" role="img" aria-label="Photo of a crane at a construction site" style="background:linear-gradient(160deg,#9fc0e0,#8a7a5e)"></div><h4>Porta lacus bibendum in</h4><p>In rhoncus urna quam, a maximus tortor dapibus eget. Nullam iaculis, ex id.</p></div>
    <div class="project"><div class="project-photo" role="img" aria-label="Photo of trucks delivering modular units" style="background:linear-gradient(160deg,#b4c6d6,#6c5c52)"></div><h4>The New One Mall</h4><p>Praesent consectetur arcu ligula, in ullamcorper nisi vestibulum sollicitudin.</p></div>
  </div>
</section>
<footer class="footer">
  <div class="f-col"><h5>K.L Marquez</h5>
    <div class="f-line"><i></i>44 Harlow Bend Road, suite 3</div>
    <div class="f-line"><i></i>Harlow Bend, CT 06700</div>
    <div class="f-line"><i></i>888-555-0147</div>
    <div class="f-line"><i></i>888-555-0148</div>
    <div class="f-line"><i></i>info@klmarquez.example</div>
  </div>
  <div class="f-col"><h5>Recently Sold</h5>
    <div class="sold-item"><div class="sold-thumb" role="img" aria-label="Thumbnail of a sold building"></div><div><p>In rhoncus urna quam, a maximus tortor.</p><b>$ 250,000</b></div></div>
    <div class="sold-item"><div class="sold-thumb" role="img" aria-label="Thumbnail of a sold building"></div><div><p>In rhoncus urna quam, a maximus tortor.</p><b>$ 180,000</b></div></div>
  </div>
  <div class="f-col social"><h5>Lets Be Social</h5><div class="social-row"><span></span><span></span><span></span><span></span></div></div>
</footer>
<div class="bottom-bar"><span>Copyright 2024 · K.L Marquez · All Rights Reserved</span><span>Privacy Policy · Terms of Use</span></div>
</body>
</html>
```